Business Card Design Project

Business Card
We are rebranding with a new logo
Industry/Entity Type
Business
Contact Information for Business Card
Dennis Morvale +61 487215963 dennis@quorv.com.au P.O. Box 872 Fernlow QLD 4309
Requirements
Must have
- Logo

```html
<!DOCTYPE html>
<html lang="en">
<head>
<meta charset="utf-8">
<title>Quorv International – Business Card</title>
<link rel="stylesheet" href="https://fonts.googleapis.com/css2?family=Open+Sans:wght@400;600;700&display=swap">
<style>
  :root {
    --bg: #e9eaec;
    --orange: #ec8a1f;
    --orange-deep: #e07b12;
    --blue: #1b8ec6;
    --blue-deep: #0f6f9f;
    --ink: #4a4d52;
    --rule: #c9cbcf;
    --white: #ffffff;
  }
  * { margin: 0; padding: 0; box-sizing: border-box; }
  html, body {
    width: 1200px; height: 960px; overflow: hidden;
    background: var(--bg);
    font-family: "Open Sans", Arial, sans-serif;
  }
  .sheet {
    width: 1200px; height: 960px;
    display: flex; flex-direction: column;
    align-items: center; justify-content: center; gap: 60px;
  }
  .card {
    position: relative;
    width: 630px; height: 360px;
    overflow: hidden;
    box-shadow: 0 6px 18px rgba(0,0,0,0.18);
  }
  /* Back side */
  .card--back {
    background: linear-gradient(135deg, var(--orange), var(--orange-deep));
    color: var(--white);
  }
  .card--back .brand {
    position: absolute; left: 0; right: 0; top: 130px;
    display: flex; align-items: center; justify-content: center; gap: 14px;
  }
  .card--back .brand-dot {
    width: 22px; height: 22px; border-radius: 50%; background: var(--white);
  }
  .card--back .brand-name {
    font-size: 34px; font-weight: 700; letter-spacing: 3px; text-transform: uppercase;
  }
  .card--back .web {
    position: absolute; left: 0; right: 0; bottom: 40px;
    text-align: center; font-size: 14px; letter-spacing: 4px;
    color: rgba(255,255,255,0.75);
  }
  /* Front side */
  .card--front { background: var(--white); }
  .card--front .brand {
    position: absolute; left: 40px; top: 122px; width: 250px;
    display: flex; align-items: center; gap: 12px;
  }
  .card--front .brand-dot {
    width: 18px; height: 18px; border-radius: 50%; background: var(--blue);
    flex: none;
  }
  .card--front .brand-name {
    font-size: 22px; font-weight: 700; letter-spacing: 2px; text-transform: uppercase;
    color: var(--blue); line-height: 1.2;
  }
  .divider {
    position: absolute; left: 315px; top: 70px; width: 1px; height: 150px;
    background: var(--rule);
  }
  .contact {
    position: absolute; left: 340px; top: 78px;
    color: var(--ink); font-size: 14px; line-height: 20px;
  }
  .contact .name {
    color: var(--blue); font-weight: 700; font-size: 16px; letter-spacing: 0.5px;
    text-transform: uppercase; margin-bottom: 12px;
  }
  .contact .address { margin-bottom: 2px; }
  .contact .line { display: flex; align-items: center; gap: 8px; }
  .contact .icon { width: 12px; height: 12px; flex: none; fill: var(--blue); }
  .swoosh { position: absolute; left: 0; bottom: 0; width: 630px; height: 130px; }
</style>
</head>
<body>
<main class="sheet">

  <section class="card card--back" aria-label="Card back">
    <div class="brand">
      <span class="brand-dot"></span>
      <span class="brand-name">Quorv International</span>
    </div>
    <p class="web">www.quorv.com.au</p>
  </section>

  <section class="card card--front" aria-label="Card front">
    <div class="brand">
      <span class="brand-dot"></span>
      <span class="brand-name">Quorv<br>International</span>
    </div>

    <div class="divider"></div>

    <div class="contact">
      <p class="name">Dennis Morvale</p>
      <p class="address">P.O. Box 872<br>Fernlow QLD 4309</p>
      <p class="line">
        <svg class="icon" viewBox="0 0 12 12"><path d="M1 4c0-2 2-3 5-3s5 1 5 3v1H8V4H4v1H1z M2 6h8l1 5H1z"/></svg>
        +61 487215963
      </p>
      <p class="line">
        <svg class="icon" viewBox="0 0 12 12"><path d="M0 2h12v1L6 7 0 3z M0 4.5l6 4 6-4V10H0z"/></svg>
        dennis@quorv.com.au
      </p>
      <p class="line">
        <svg class="icon" viewBox="0 0 12 12"><circle cx="6" cy="6" r="5.5"/><circle cx="6" cy="6" r="2" fill="#fff"/></svg>
        www.quorv.com.au
      </p>
    </div>

    <svg class="swoosh" viewBox="0 0 630 130" preserveAspectRatio="none" aria-hidden="true">
      <defs>
        <linearGradient id="bandFill" x1="0" y1="0" x2="0" y2="1">
          <stop offset="0" stop-color="#2aa3d8"/>
          <stop offset="1" stop-color="#0f6f9f"/>
        </linearGradient>
      </defs>
      <path d="M0 12 C180 50 420 80 630 78 L630 130 L0 130 Z" fill="url(#bandFill)"/>
      <path d="M0 30 C200 70 420 96 630 94" stroke="#ffffff" stroke-width="4" fill="none"/>
      <path d="M0 0 C180 40 420 70 630 70" stroke="#1b8ec6" stroke-width="1.5" fill="none"/>
    </svg>
  </section>

</main>
</body>
</html>
```